School Website

I need a design for a School (2 sections: Primary 6-12 years and Secondary 12-18 years). The first page is just a choice of the 2 sections. After we'll need 2 websites (with the same structure: Menu, ...) but with different colors. In fact, we need for end of October, 6 design of school website. So the best websites are going to be made available to you in the future (in pixelharbor) but privately.

Target Market(s)

Public, Parents, ...

Coding

Coded - Design and coding required

Number of Pages Required

5+ page

Font styles to use
Sans Serif

Colors
34a6d7
85cae6
cee9f5
ffffff

Requirements
Must have
• You can check the old Website: http: / /velmot.be We need the same pages with the same content. Menu: - HomePage - News and communication (like blog page) - Activities (like blog page, with photo gallery) - Contact (Contact form + maps) - In the main menu, we need a special button to connect to an external Website ( button needs to be different than the other menu items The name of this button is "Parents Area"). The logo of 2 sections are attached. Please use it for the design and the choice of colors.
Nice to have
• This is a web design of other school that we like: https://www.quintelo.be

```html
<!DOCTYPE html>
<html lang="fr">
<head>
<meta charset="utf-8">
<title>Athénée Royal de Velmot</title>
<link href="https://fonts.googleapis.com/css2?family=Raleway:ital,wght@0,400;0,500;0,600;0,700;1,400&display=swap" rel="stylesheet">
<style>
:root{
  --blue:#34a6d7;
  --blue-mid:#85cae6;
  --blue-pale:#cee9f5;
  --white:#ffffff;
  --ink:#2b2b2b;
  --text:#555b60;
  --orange:#f15a2b;
  --board:#3a3a3a;
}
*{margin:0;padding:0;box-sizing:border-box}
html,body{width:686px;height:1200px;overflow:hidden;background:var(--white)}
body{font-family:"Raleway",sans-serif;color:var(--ink);position:relative}
.page{position:absolute;left:103px;top:1px;width:1020px;height:2462px;transform:scale(0.4712);transform-origin:0 0}
.abs{position:absolute}

/* hero */
.hero{position:absolute;left:0;top:0;width:1020px;height:500px;overflow:hidden}
.hero-bg{position:absolute;inset:0;background:linear-gradient(100deg,#2e2e2e 0%,#3d3d3d 45%,#4a4a4a 100%)}
.hero-photo{position:absolute;left:540px;top:90px;width:390px;height:410px;border-radius:190px 190px 0 0;background:linear-gradient(180deg,#8a6a4c 0%,#6f8fae 55%,#5c7ea0 100%)}
.brand{position:absolute;left:15px;top:18px;display:flex;align-items:center;gap:6px;color:var(--white);font-weight:700;font-size:14px}
.brand-dot{width:14px;height:14px;border-radius:50%;background:#7cc04b}
.nav{position:absolute;top:25px;left:0;font-size:15px;font-weight:500;color:var(--white)}
.nav span{position:absolute;white-space:nowrap}
.parents-btn{position:absolute;left:896px;top:13px;width:113px;height:45px;border-radius:10px;background:var(--orange);color:var(--white);font-weight:600;font-size:15px;display:flex;align-items:center;justify-content:center}
.hero-rule{position:absolute;left:385px;top:45px;width:1px;height:455px;background:rgba(255,255,255,.55)}
.hero-title{position:absolute;left:18px;top:128px;font-size:38px;font-weight:600;color:var(--white);white-space:nowrap}
.hero-title b{color:var(--blue);font-weight:600}
.hero-sub{position:absolute;left:17px;top:186px;font-size:22px;font-weight:500;color:var(--blue-pale)}
.hero-copy{position:absolute;left:18px;top:233px;width:240px;font-size:15px;line-height:22px;color:var(--white)}
.partner{position:absolute;left:22px;top:440px;display:flex;align-items:center;gap:6px;color:var(--white);font-size:12px;font-weight:600}
.partner i{width:12px;height:12px;background:var(--orange);display:block}

/* big headings */
.big{position:absolute;font-size:54px;line-height:60px;font-weight:500;letter-spacing:1px;color:var(--ink)}
.big .hl{color:var(--blue)}
.para{position:absolute;font-size:14px;line-height:22px;color:var(--text)}

.mark{position:absolute;left:20px;top:570px;width:36px;height:36px;display:flex;align-items:center;justify-content:center;color:var(--blue);font-size:10px;font-weight:700}
.mark i{width:18px;height:18px;border-radius:50%;background:#7cc04b;display:block}
.meta{position:absolute;top:857px;font-size:13px;color:var(--text)}

/* bands */
.band{position:absolute;left:0;width:1020px;background:var(--blue-pale)}
.arrow{position:absolute;width:22px;height:40px}
.dots{position:absolute;display:flex;gap:10px}
.dots i{width:8px;height:8px;border-radius:50%;border:1.5px solid var(--blue);display:block}
.dots i:first-child{background:var(--blue)}
.avatar{position:absolute;width:70px;height:70px;border-radius:50%;border:3px solid var(--blue-mid);background:linear-gradient(160deg,#c79a7a,#7a5a44)}
.person{position:absolute;left:204px;width:190px}
.person h4{font-size:15px;font-weight:500;color:var(--ink)}
.person em{display:block;font-size:12px;color:var(--text);margin:4px 0 6px}
.person p{font-size:14px;line-height:21px;color:var(--text)}
.person a{display:block;font-size:14px;color:var(--blue);text-decoration:none;margin-top:3px}
.icon-fill{position:absolute;border-radius:6px}

.list{position:absolute;left:518px;top:1376px;width:420px;list-style:none;font-size:14px;line-height:22px;color:var(--text)}
.list li{position:relative;padding-left:12px;margin-bottom:8px}
.list li::before{content:"";position:absolute;left:0;top:7px;width:4px;height:4px;border-radius:50%;background:var(--ink)}
.link-orange{color:var(--orange);font-size:14px}

/* footer */
.footer{position:absolute;left:0;top:2028px;width:1020px;height:434px;background:#31a8dc;color:var(--white)}
.footer h3{position:absolute;left:17px;top:40px;font-size:15px;font-weight:600}
.field{position:absolute;border-bottom:1px solid var(--white);font-size:11px;font-style:italic;padding-left:2px}
.send{position:absolute;left:18px;top:220px;width:110px;height:36px;border:1.5px solid var(--white);border-radius:4px;display:flex;align-items:center;justify-content:center;font-size:15px}
.addr{position:absolute;left:17px;top:280px;font-size:13px;line-height:22px}
.social{position:absolute;left:18px;top:380px;display:flex;gap:9px}
.social i{width:28px;height:28px;border-radius:50%;background:var(--blue-pale);display:block}
.copy{position:absolute;left:0;width:1020px;top:411px;text-align:center;font-size:11px;color:var(--blue-pale)}
.map{position:absolute;left:518px;top:42px;width:480px;height:260px;background:linear-gradient(135deg,#5ab8e2,#3aa4d6)}
</style>
</head>
<body>
<div class="page">

  <header class="hero">
    <div class="hero-bg" role="img" aria-label="Chalkboard background"></div>
    <div class="hero-photo" role="img" aria-label="Photo of a schoolgirl in glasses holding colourful folders"></div>
    <div class="brand"><span class="brand-dot"></span>Velmot</div>
    <nav class="nav">
      <span style="left:123px">maternelle-primaire</span>
      <span style="left:300px">secondaire</span>
      <span style="left:407px">Activités</span>
      <span style="left:497px">Galerie</span>
      <span style="left:577px">Contactez-nous</span>
    </nav>
    <div class="parents-btn">Zone Parents</div>
    <div class="hero-rule"></div>
    <h1 class="hero-title"><b>Athénée Royal</b> de Velmot</h1>
    <h2 class="hero-sub">Maternelles et Primaires</h2>
    <p class="hero-copy">Lorem ipsum dolor sit amet, consectetur adipiscing elit. Phasellus ultricies lectus a nibh luctus, ut malesuada magna</p>
    <div class="partner"><i></i>Velmot Réseau</div>
  </header>

  <section class="about">
    <div class="mark"><i></i></div>
    <h2 class="big" style="left:18px;top:606px">Sur<br><span class="hl">Athénée Royal</span><br>de Velmot</h2>
    <p class="para" style="left:592px;top:609px;width:330px">Lorem ipsum dolor sit amet, consectetur adipiscing elit. Phasellus ultricies lectus a nibh luctus, ut malesuada magna accumsan. Donec consectetur, quam et pretium feugiat, ligula orci viverra purus, et lacinia lectus sapien vel metus. Praesent sed sem tortor. Nunc ac est nisl. Curabitur consectetur luctus velit id maximus. Praesent facilisis sodales</p>
    <p class="meta" style="left:17px">Rue des Tilleuls 12, 4520 Velmot, Belgique</p>
    <p class="meta" style="left:402px">+32-81 40 55 17</p>
  </section>

  <section class="band staff" style="top:905px;height:368px">
    <svg class="arrow" style="left:18px;top:148px" viewBox="0 0 22 40"><path d="M20 2 L3 20 L20 38" fill="none" stroke="#34a6d7" stroke-width="2.5"/></svg>
    <svg class="arrow" style="left:466px;top:148px" viewBox="0 0 22 40"><path d="M2 2 L19 20 L2 38" fill="none" stroke="#34a6d7" stroke-width="2.5"/></svg>

    <div class="avatar" style="left:112px;top:40px" role="img" aria-label="Portrait of Nora Delcourt"></div>
    <div class="person" style="top:47px">
      <h4>Nora Delcourt</h4><em>science</em>
      <p>Lorem ipsum dolor sit amet, consectetur adipiscing elit. Phasellus</p>
      <a>noradelcourt@velmot.be</a>
    </div>
    <div class="avatar" style="left:112px;top:190px" role="img" aria-label="Portrait of Lise Vandamme"></div>
    <div class="person" style="top:197px">
      <h4>Lise Vandamme</h4><em>math</em>
      <p>Lorem ipsum dolor sit amet, consectetur adipiscing elit. Phasellus</p>
      <a>lisevandamme@velmot.be</a>
    </div>
    <div class="dots" style="left:207px;top:351px"><i></i><i></i><i></i><i></i><i></i></div>

    <div class="icon-fill" style="left:858px;top:40px;width:48px;height:50px;background:linear-gradient(180deg,#4b5a78,#c1805a)" role="img" aria-label="Illustration of a teacher in a graduation cap"></div>
    <h2 class="big" style="left:590px;top:92px">Rencontrez<br>notre<br><span class="hl">personnel</span></h2>
  </section>

  <section class="calendar">
    <div class="icon-fill" style="left:19px;top:1318px;width:44px;height:48px;background:linear-gradient(180deg,#8a5fc0 0 28%,#f1f1f4 28%)" role="img" aria-label="Calendar icon"></div>
    <h2 class="big" style="left:18px;top:1371px"><span class="hl">Calenderier</span><br>et<br>Vacances</h2>
    <ul class="list">
      <li>L’établissement sera ouvert jusqu’au 5 juillet 2018 inclus et à partir du 16 août 2018 de 9h à 15h.</li>
      <li>Rentrée scolaire: lundi 3 septembre.</li>
      <li>Fête de la Communauté française : jeudi 27 septembre.</li>
      <li>Congé d’automne (Toussaint) : Du lundi 29 octobre au vendredi 2 novembre 2018</li>
      <li>Vacances d’hiver (Noël) : Du lundi 24 décembre 2018 au vendredi 4 janvier 2019</li>
    </ul>
    <a class="abs link-orange" style="left:820px;top:1633px">voir le calendrier complet</a>
  </section>

  <section class="band news" style="top:1674px;height:354px">
    <svg class="arrow" style="left:18px;top:144px" viewBox="0 0 22 40"><path d="M20 2 L3 20 L20 38" fill="none" stroke="#34a6d7" stroke-width="2.5"/></svg>
    <svg class="arrow" style="left:464px;top:144px" viewBox="0 0 22 40"><path d="M2 2 L19 20 L2 38" fill="none" stroke="#34a6d7" stroke-width="2.5"/></svg>
    <p class="para" style="left:101px;top:88px;width:295px">Visite du rucher école de la ville de Velmot avec les 6èmes Sciences – génétique et écologie des pollinisateurs.<br><span style="color:var(--orange)">Lire la suite</span></p>
    <p class="para" style="left:101px;top:202px;font-size:10px;font-style:italic;line-height:21px">18 septembre 2018<br>rucher école, ville de Velmot</p>
    <div class="dots" style="left:224px;top:332px"><i></i><i></i><i></i><i></i></div>
    <div class="icon-fill" style="left:823px;top:34px;width:50px;height:50px;border-radius:50%;background:var(--orange)" role="img" aria-label="News globe icon"></div>
    <h2 class="big" style="left:592px;top:84px"><span class="hl">Nouvelles</span><br>et<br>Activites</h2>
  </section>

  <footer class="footer">
    <h3>Contactez-nous</h3>
    <div class="field" style="left:17px;top:84px;width:138px">Nom</div>
    <div class="field" style="left:167px;top:84px;width:138px">Adresse e-mail</div>
    <div class="field" style="left:17px;top:143px;width:288px;height:52px">Message</div>
    <div class="send">Envoyer</div>
    <p class="addr">Rue des Tilleuls 12,<br>4520 Velmot, Belgique<br>+32-81 40 55 17<br>Du lundi au vendredi 7.00- 18.00</p>
    <div class="social"><i></i><i></i><i></i></div>
    <div class="map" role="img" aria-label="Street map of Velmot with the school location marked"></div>
    <p class="copy">2019 Tous droits réservés. Athénée Royal de Velmot</p>
  </footer>

</div>
</body>
</html>
```